Maple Roster Business Card for recruitment company

We are looking for a Business Card Design that incorporates our personal details and our busines name and logo. We are a specialized search consultancy that recruit Property and Construction professionals.
We would like a business card that stands out and is appealing to the Construction and Property industry as well.

Target Market(s)

people in the construction and property industry

Contact Information for Business Card

Business Name and logo

Font styles to use
Serif

Colors
0094D4
00A9DD
6FCCEA
C7EBF8
E9F6FB

Requirements
Must have
• Business name and logo as well as contact details
Should not have
• No photos of us please

```html
<!DOCTYPE html>
<html lang="en">
<head>
<meta charset="utf-8">
<title>Maple Roster — Business Card</title>
<link href="https://fonts.googleapis.com/css2?family=Lato:wght@300;400;700&display=swap" rel="stylesheet">
<style>
  :root {
    --backdrop: #e4e4e4;
    --paper: #ffffff;
    --teal-light: #006c7e;
    --teal-dark: #00304a;
    --ink-teal: #0b5a6b;
    --ink-white: #ffffff;
    --rule: rgba(255,255,255,0.75);
  }
  * { margin: 0; padding: 0; box-sizing: border-box; }
  html, body { width: 1200px; height: 1200px; overflow: hidden; }
  body {
    background: var(--backdrop);
    font-family: "Lato", sans-serif;
    position: relative;
  }
  .card {
    position: absolute;
    left: 262px;
    width: 686px;
    height: 392px;
    overflow: hidden;
    box-shadow: 0 18px 30px rgba(0,0,0,0.18);
  }
  .card--front { top: 165px; background: var(--paper); }
  .card--back {
    top: 653px;
    background: linear-gradient(to top right, var(--teal-dark) 0%, var(--teal-light) 100%);
  }
  .wordmark {
    position: absolute;
    left: 0; right: 0;
    text-align: center;
    font-family: "Lato", sans-serif;
    font-weight: 300;
    font-size: 62px;
    letter-spacing: 3px;
    line-height: 1;
    text-transform: uppercase;
  }
  .card--front .wordmark { top: 96px; color: var(--ink-teal); }
  .card--back .wordmark { top: 162px; color: var(--ink-white); }
  .contact-band {
    position: absolute;
    left: 0; right: 0;
    top: 209px; bottom: 0;
    background: linear-gradient(to top right, var(--teal-dark) 0%, var(--teal-light) 100%);
    color: var(--ink-white);
  }
  .stitch-line {
    position: absolute;
    left: 0; right: 0; top: 7px;
    border-top: 1px dashed var(--rule);
  }
  .identity {
    position: absolute;
    right: 357px;
    top: 40px;
    text-align: right;
    font-size: 15px;
    line-height: 19px;
  }
  .identity .person-name {
    font-weight: 700;
    font-size: 22px;
    line-height: 26px;
    letter-spacing: 0.3px;
  }
  .identity .person-role { margin-bottom: 6px; }
  .divider {
    position: absolute;
    left: 342px;
    top: 42px;
    height: 90px;
    border-left: 1px dashed var(--rule);
  }
  .contact-list {
    position: absolute;
    left: 354px;
    top: 40px;
    list-style: none;
    font-size: 15.5px;
    line-height: 19.5px;
  }
  .contact-list li { display: flex; align-items: center; gap: 9px; }
  .contact-list svg { width: 12px; height: 12px; fill: var(--ink-white); flex: none; }
</style>
</head>
<body>

<section class="card card--front">
  <div class="wordmark">Maple Roster</div>
  <div class="contact-band">
    <div class="stitch-line"></div>
    <div class="identity">
      <div class="person-name">DANIEL REYES</div>
      <div class="person-role">President</div>
      <div>2140 Cedar Hollow Rd</div>
      <div>Fairbanks, Alaska 34821</div>
    </div>
    <div class="divider"></div>
    <ul class="contact-list">
      <li><svg viewBox="0 0 12 12"><path d="M2.5 0.5l2 2.4-1.1 1.3c.7 1.6 2 2.9 3.5 3.6l1.3-1.1 2.4 2-1.3 2C5.2 10.4 1.6 6.8.5 2.2z"/></svg>369-408-1172</li>
      <li><svg viewBox="0 0 12 12"><path d="M3 0h6v12H3zM4 1.2v8.3h4V1.2zM5.4 10.2h1.2v1H5.4z" fill-rule="evenodd"/></svg>369-627-3019</li>
      <li><svg viewBox="0 0 12 12"><path d="M3 0h5l1 1v3H3zM0 5h12v5H10v2H2v-2H0zM3 8v3h6V8z" fill-rule="evenodd"/></svg>369-754-2860</li>
      <li><svg viewBox="0 0 12 12"><path d="M0 2.5h12v7H0zM.8 3.2L6 6.8l5.2-3.6"/><path d="M.6 3.1L6 6.9l5.4-3.8" stroke="#00405a" stroke-width="1" fill="none"/></svg>daniel@mapleroster.com</li>
      <li><svg viewBox="0 0 12 12"><circle cx="6" cy="6" r="5.8"/><path d="M3 3.2c1 .2 1.6 1 1.3 2-.3.8.6 1.3.4 2.3-.2.8-.9 1.4-.8 2.4M7.5 1.3c-.4 1 .4 1.6 1.2 1.8.9.2 1 1.2.5 1.8-.5.7.3 1.6 1.6 1.3" stroke="#00405a" stroke-width="1" fill="none"/></svg>www.mapleroster.com</li>
    </ul>
  </div>
</section>

<section class="card card--back">
  <div class="wordmark">Maple Roster</div>
</section>

</body>
</html>
```